Creative, fresh business card design for Ripplecraft Facades

We need a fresh, creative business card design for Ripplecraft Facades. We are the manufacturer of Ripplecraft Facades in Australia. Wall panels are 2400 x 1200mm panels made from MDF and feature 3D patterns on the face of the panel. The colours to be used are green, silver/grey and white RGB
Red 187
Green 207
Blue 65.

An idea is to possibly use a watermark of one of our designs as a background (like on the "Grids" design on the left hand side of page 2 of our brochure).

Target Market(s)

Interior designers, architects, builders and home renovators

Industry/Entity Type

Business

Contact Information for Business Card

Details to go on the card are:
Our logo (attached),
Slogan: "Decorative panels for interiors and exteriors",
Contact name,
Position,
Mobile phone number,
Business address,
Business phone,
Business fax,
Website and
Email address.

I have attached a few images of our panels and our brochure for reference.

The colours of the business card should feature our logo colours which are: RGB
Red 187
Green 207
Blue 65

Requirements
Must have
• Very modern fonts and design. Some of the designs shown especially the "Prisms" design which is a popular design.
Nice to have
• Creative but simple design. Very contemporary.
Should not have
• Anything ornate or old fashioned.

```html
<!DOCTYPE html>
<html lang="en">
<head>
<meta charset="utf-8">
<title>Ripplecraft Facades – Business Card</title>
<link rel="stylesheet" href="https://fonts.googleapis.com/css2?family=Open+Sans:wght@400;600;700&display=swap">
<style>
  :root {
    --brand-green: rgb(187, 207, 65);
    --brand-grey: #8e8f92;
    --text-grey: #555659;
    --card-white: #ffffff;
    --backdrop: #5b4b3d;
    --shadow: rgba(0, 0, 0, 0.35);
  }
  * { box-sizing: border-box; margin: 0; padding: 0; }
  html, body {
    width: 1200px; height: 987px; overflow: hidden;
    background: var(--backdrop);
    font-family: "Open Sans", Arial, sans-serif;
  }
  .canvas { position: relative; width: 1200px; height: 987px; }

  .card {
    position: absolute; width: 615px; height: 352px;
    box-shadow: 2px 3px 6px var(--shadow);
  }
  .card--front { left: 293px; top: 130px; background: var(--card-white); }
  .card--back { left: 292px; top: 505px; background: var(--brand-green); }

  /* Front: brand block */
  .brand { position: absolute; left: 35px; top: 32px; }
  .brand__name {
    display: flex; align-items: center; gap: 10px;
    font-size: 22px; font-weight: 600; color: var(--brand-grey);
  }
  .brand__mark { width: 22px; height: 22px; background: var(--brand-green); }
  .brand__slogan {
    margin-top: 8px; font-size: 11px; line-height: 13px;
    letter-spacing: 2.2px; color: var(--brand-grey);
  }

  /* Front: contact list */
  .address {
    position: absolute; left: 35px; top: 180px;
    font-size: 16px; line-height: 24px; color: var(--text-grey);
  }
  .contacts {
    position: absolute; left: 35px; top: 232px; list-style: none;
    font-size: 16px; line-height: 24px; color: var(--text-grey);
  }
  .contacts li { display: flex; align-items: center; gap: 9px; }
  .contacts svg { width: 15px; height: 15px; flex: none; fill: var(--brand-green); }

  /* Front: name band */
  .name-band__accent {
    position: absolute; left: 367px; top: 213px; width: 15px; height: 84px;
    background: var(--brand-grey);
  }
  .name-band {
    position: absolute; left: 384px; top: 213px; width: 231px; height: 84px;
    background: var(--brand-green); color: var(--card-white);
    text-align: right; padding: 16px 38px 0 0;
  }
  .name-band__name { font-size: 21px; font-weight: 700; line-height: 26px; }
  .name-band__role { font-size: 16px; line-height: 22px; }

  /* Back */
  .back-brand {
    position: absolute; left: 0; right: 0; top: 118px;
    display: flex; justify-content: center; align-items: center; gap: 12px;
    font-size: 28px; font-weight: 600; color: var(--card-white);
  }
  .back-brand__mark { width: 28px; height: 28px; background: var(--card-white); }
  .back-slogan {
    position: absolute; left: 0; right: 0; top: 227px; text-align: center;
    font-size: 13px; line-height: 17px; letter-spacing: 3px; color: var(--card-white);
  }
  .back-web {
    position: absolute; left: 0; right: 0; top: 290px; text-align: center;
    font-size: 15px; letter-spacing: 3.2px; color: var(--card-white);
  }
</style>
</head>
<body>
<main class="canvas">
  <section class="card card--front">
    <div class="brand">
      <div class="brand__name"><span class="brand__mark"></span>Ripplecraft Facades</div>
      <p class="brand__slogan">decorative panels for<br>interiors &amp; landscapes</p>
    </div>

    <p class="address">42 Harbour Street<br>Geelong, Victoria 3220</p>

    <ul class="contacts">
      <li><svg viewBox="0 0 16 16" aria-hidden="true"><path d="M4 1l3 3-2 2c1 2 3 4 5 5l2-2 3 3-2 3C7 15 1 9 1 3z"/></svg>(03) 555-0142</li>
      <li><svg viewBox="0 0 16 16" aria-hidden="true"><rect x="4" y="1" width="8" height="5"/><rect x="1" y="7" width="14" height="6" rx="1"/><rect x="4" y="11" width="8" height="4" fill="#fff"/></svg>(03) 555-0187</li>
      <li><svg viewBox="0 0 16 16" aria-hidden="true"><path d="M1 3h14v10H1z"/><path d="M1 3l7 6 7-6" fill="none" stroke="#fff" stroke-width="1.4"/></svg>lcarter@ripplecraftfacades.com</li>
      <li><svg viewBox="0 0 16 16" aria-hidden="true"><circle cx="8" cy="8" r="7"/><path d="M1 8h14M8 1c-3 3-3 11 0 14M8 1c3 3 3 11 0 14" fill="none" stroke="#fff" stroke-width="1"/></svg>www.ripplecraftfacades.com</li>
    </ul>

    <div class="name-band__accent"></div>
    <div class="name-band">
      <p class="name-band__name">LIAM CARTER</p>
      <p class="name-band__role">CEO&amp;Founder</p>
    </div>
  </section>

  <section class="card card--back">
    <div class="back-brand"><span class="back-brand__mark"></span>Ripplecraft Facades</div>
    <p class="back-slogan">decorative panels for<br>interiors &amp; landscapes</p>
    <p class="back-web">www.ripplecraftfacades.com</p>
  </section>
</main>
</body>
</html>
```